Brickfield real estate investment company needs a poster design

We would like a poster design size 18 x 24.
Poster wording -
I WANT TO BUY YOUR ( finish with logo) logo uploaded
website- www.brickfield.example
phone # 555-218-7043 ( color red for the phone number)
we would like to see the poster on 2 different backgrounds
Yellow background
White background
horizontal

```html
<!DOCTYPE html>
<html lang="en">
<head>
<meta charset="utf-8">
<title>Brickfield – I Want To Buy Your House</title>
<link rel="stylesheet" href="https://fonts.googleapis.com/css2?family=Oswald:wght@500;700&family=Nunito:wght@800&display=swap">
<style>
  :root {
    --signal-red: #e21f26;
    --sun-yellow: #fcec04;
    --ink-black: #000000;
    --paper-white: #ffffff;
  }
  html, body {
    margin: 0;
    padding: 0;
    width: 1200px;
    height: 900px;
    overflow: hidden;
    background: var(--paper-white);
  }
  .poster {
    display: block;
    width: 1200px;
    height: 900px;
  }
  .band-red { fill: var(--signal-red); }
  .band-yellow { fill: var(--sun-yellow); }
  .band-black { fill: var(--ink-black); }
  .headline {
    font-family: "Oswald", sans-serif;
    font-weight: 500;
    fill: var(--paper-white);
  }
  .brand-name {
    font-family: "Oswald", sans-serif;
    font-weight: 700;
    fill: var(--ink-black);
  }
  .web-address {
    font-family: "Nunito", sans-serif;
    font-weight: 800;
    fill: var(--sun-yellow);
  }
  .phone-number {
    font-family: "Oswald", sans-serif;
    font-weight: 500;
    fill: var(--paper-white);
  }
  .phone-badge { fill: var(--paper-white); }
  .phone-icon { fill: var(--ink-black); }
</style>
</head>
<body>
<svg class="poster" viewBox="0 0 1200 900" xmlns="http://www.w3.org/2000/svg" role="img" aria-label="I want to buy your house – Brickfield – www.brickfield.example – 555-218-7043">
  <rect class="band-red" x="0" y="0" width="1200" height="900"/>
  <path class="band-yellow" d="M0 238 C150 170 400 130 600 190 C800 245 1000 260 1200 220 L1200 900 L0 900 Z"/>
  <path class="band-black" d="M0 506 C150 450 450 450 700 480 C900 500 1050 500 1200 450 L1200 900 L0 900 Z"/>
  <path class="band-red" d="M0 832 C60 760 200 660 500 650 C750 645 950 720 1200 680 L1200 900 L0 900 Z"/>

  <text class="headline" x="40" y="160" font-size="160" textLength="1128" lengthAdjust="spacingAndGlyphs">I WANT TO BUY YOUR</text>

  <text class="brand-name" x="600" y="424" font-size="150" text-anchor="middle" textLength="900" lengthAdjust="spacingAndGlyphs">BRICKFIELD</text>

  <text class="web-address" x="64" y="610" font-size="84" textLength="1044" lengthAdjust="spacingAndGlyphs">www.brickfield.example</text>

  <g class="phone-contact">
    <circle class="phone-badge" cx="132" cy="766" r="100"/>
    <path class="phone-icon" d="M96 702 L106 695 Q110 693 113 697 L126 716 Q128 720 124 723 L114 730 Q110 733 112 738 Q120 764 143 787 Q147 790 151 786 L159 779 Q163 776 166 780 L177 797 Q179 801 175 804 L166 811 Q160 815 150 812 Q118 800 100 767 Q86 740 88 714 Q89 706 96 702 Z"/>
    <text class="phone-number" x="252" y="852" font-size="150" textLength="908" lengthAdjust="spacingAndGlyphs">555-218-7043</text>
  </g>
</svg>
</body>
</html>
```